Cafe Business needs a business card design

I already have an ai logo I would like to use and color. I need someone to make a business card for me on adobe illustrator with it. Its for a cafe restaurant opening in Japan I would like to be able to change out the names, contact info, ect on my own from adobe illustrator.

Industry/Entity Type

Business

Contact Information for Business Card

Double sided with logo on one side and info on the other. Name, Tel, fax, email and west

```html
<!DOCTYPE html>
<html lang="en">
<head>
<meta charset="utf-8">
<title>Kumo Bean Cafe – Business Card</title>
<link rel="stylesheet" href="https://fonts.googleapis.com/css2?family=Open+Sans:wght@400;600;700&display=swap">
<style>
  :root {
    --bg: #ece8e3;
    --espresso-dark: #2e1a10;
    --espresso: #4a2d1e;
    --espresso-light: #6b4632;
    --cream: #f1e8da;
    --cream-deep: #e2d3bd;
    --white: #ffffff;
    --ink: #3b2418;
    --ink-soft: #5a4030;
  }
  * { margin: 0; padding: 0; box-sizing: border-box; }
  html, body { width: 1200px; height: 913px; overflow: hidden; }
  body {
    background: var(--bg);
    font-family: "Open Sans", Arial, sans-serif;
    position: relative;
  }
  .card {
    position: absolute;
    width: 520px;
    height: 300px;
    border-radius: 18px;
    overflow: hidden;
    box-shadow: 0 10px 28px rgba(40, 25, 15, 0.25);
  }
  .card-front { left: 50px; top: 306px; }
  .card-back  { left: 630px; top: 306px; }
  .card svg.card-art { position: absolute; inset: 0; }

  .brand {
    position: absolute;
    display: flex;
    align-items: center;
    gap: 14px;
  }
  .brand-square { width: 62px; height: 62px; flex: none; }
  .brand-name {
    font-weight: 700;
    font-size: 22px;
    line-height: 1.08;
    letter-spacing: 1px;
    white-space: nowrap;
  }
  .card-front .brand { left: 34px; top: 112px; }
  .card-front .brand-square { background: var(--white); }
  .card-front .brand-name { color: var(--white); }
  .card-back .brand { right: 40px; top: 46px; }
  .card-back .brand-square { background: var(--espresso); }
  .card-back .brand-name { color: var(--espresso); }

  .contact {
    position: absolute;
    right: 22px;
    top: 70px;
    text-align: right;
    color: var(--ink);
  }
  .contact-name { font-size: 18px; font-weight: 600; letter-spacing: 0.5px; line-height: 24px; white-space: nowrap; }
  .contact-role { font-size: 11px; color: var(--ink-soft); margin-bottom: 8px; letter-spacing: 0.5px; }
  .contact-line {
    display: flex;
    justify-content: flex-end;
    align-items: center;
    gap: 7px;
    font-size: 11px;
    line-height: 18px;
    white-space: nowrap;
  }
  .contact-line svg { width: 10px; height: 10px; flex: none; }
</style>
</head>
<body>

<!-- Front side: info -->
<div class="card card-front">
  <svg class="card-art" width="520" height="300" viewBox="0 0 520 300">
    <defs>
      <linearGradient id="espressoFront" x1="0" y1="0" x2="1" y2="1">
        <stop offset="0" stop-color="var(--espresso-dark)"/>
        <stop offset="0.6" stop-color="var(--espresso)"/>
        <stop offset="1" stop-color="var(--espresso-light)"/>
      </linearGradient>
      <linearGradient id="creamFront" x1="0" y1="0" x2="1" y2="1">
        <stop offset="0" stop-color="var(--cream)"/>
        <stop offset="1" stop-color="var(--cream-deep)"/>
      </linearGradient>
    </defs>
    <rect width="520" height="300" fill="url(#creamFront)"/>
    <path d="M0 0 H252 C322 60 342 180 347 300 H0 Z" fill="var(--white)"/>
    <path d="M0 0 H240 C310 60 330 180 335 300 H0 Z" fill="url(#espressoFront)"/>
  </svg>

  <div class="brand">
    <div class="brand-square"></div>
    <div class="brand-name">KUMO BEAN<br>CAFE</div>
  </div>

  <div class="contact">
    <div class="contact-name">KEN ARATA</div>
    <div class="contact-role">OWNER</div>
    <div class="contact-line">+33 2415-7730
      <svg viewBox="0 0 12 12"><path d="M3 1 L5 3.5 L4 5 C5 7 6 8 7.5 8.5 L9 7.5 L11 9.5 L9.5 11 C5 10.5 1.5 7 1 2.5 Z" fill="var(--ink-soft)"/></svg>
    </div>
    <div class="contact-line">+33-2415-7731
      <svg viewBox="0 0 12 12"><rect x="1" y="4" width="10" height="6" rx="1" fill="var(--ink-soft)"/><rect x="3" y="1" width="6" height="3" fill="var(--ink-soft)"/></svg>
    </div>
    <div class="contact-line">kenarata@mailbox.com
      <svg viewBox="0 0 12 12"><rect x="1" y="2.5" width="10" height="7" rx="1" fill="var(--ink-soft)"/><path d="M1.5 3 L6 6.5 L10.5 3" stroke="var(--cream)" fill="none"/></svg>
    </div>
    <div class="contact-line">www.kumobeancafe.com
      <svg viewBox="0 0 12 12"><circle cx="6" cy="6" r="5" fill="var(--ink-soft)"/><path d="M1 6 H11 M6 1 C3.5 3.5 3.5 8.5 6 11 M6 1 C8.5 3.5 8.5 8.5 6 11" stroke="var(--cream)" stroke-width="0.7" fill="none"/></svg>
    </div>
  </div>
</div>

<!-- Back side: name mark -->
<div class="card card-back">
  <svg class="card-art" width="520" height="300" viewBox="0 0 520 300">
    <defs>
      <linearGradient id="espressoBack" x1="0" y1="0" x2="1" y2="1">
        <stop offset="0" stop-color="var(--espresso-dark)"/>
        <stop offset="0.55" stop-color="var(--espresso)"/>
        <stop offset="1" stop-color="var(--espresso-light)"/>
      </linearGradient>
      <linearGradient id="creamBack" x1="0" y1="0" x2="1" y2="1">
        <stop offset="0" stop-color="var(--cream)"/>
        <stop offset="1" stop-color="var(--cream-deep)"/>
      </linearGradient>
    </defs>
    <rect width="520" height="300" fill="url(#creamBack)"/>
    <path d="M0 158 C120 205 300 225 520 214 V300 H0 Z" fill="var(--white)"/>
    <path d="M0 168 C120 215 300 235 520 224 V300 H0 Z" fill="url(#espressoBack)"/>
  </svg>

  <div class="brand">
    <div class="brand-square"></div>
    <div class="brand-name">KUMO BEAN<br>CAFE</div>
  </div>
</div>

</body>
</html>
```